Im open to ideas.. I was thinking on my business cards aswell as my logo. a place for my name. email. phone number and abn..

ive attched a file with my business logo. which i dont love the colours.. i was think a dark background with charcoal letters so something along those colour schumes but im open to ideas..

BRM Constructions

```html
<!DOCTYPE html>
<html lang="en">
<head>
<meta charset="utf-8">
<title>Example Constructions – Business Card</title>
<link rel="stylesheet" href="https://fonts.googleapis.com/css2?family=Jura:wght@500;600&display=swap">
<style>
  :root {
    --backdrop: #7e7e7e;
    --card-white: #ffffff;
    --card-charcoal: #3d3d3d;
    --accent-red: #e3161f;
    --ink-charcoal: #3a3a3a;
    --ink-light: #ffffff;
  }
  * { box-sizing: border-box; margin: 0; padding: 0; }
  html, body {
    width: 1200px;
    height: 852px;
    overflow: hidden;
    background: var(--backdrop);
  }
  .canvas {
    position: relative;
    width: 1200px;
    height: 852px;
  }
  .business-card {
    position: absolute;
    left: 232px;
    top: 187px;
    width: 758px;
    height: 463px;
    border-radius: 18px;
    overflow: hidden;
    display: flex;
    background: var(--card-charcoal);
  }
  .brand-side {
    width: 364px;
    height: 100%;
    background: var(--card-white);
    display: flex;
    align-items: center;
    justify-content: center;
  }
  .brand-name {
    font-family: "Jura", sans-serif;
    font-weight: 600;
    font-size: 28px;
    letter-spacing: 0.5px;
    white-space: nowrap;
    color: var(--ink-charcoal);
    margin-top: 40px;
  }
  .accent-bar {
    width: 12px;
    height: 100%;
    background: var(--accent-red);
  }
  .contact-side {
    position: relative;
    flex: 1;
    height: 100%;
    font-family: "Jura", sans-serif;
    color: var(--ink-light);
  }
  .person-name {
    position: absolute;
    right: 48px;
    top: 156px;
    font-weight: 600;
    font-size: 31px;
    letter-spacing: 2px;
    white-space: nowrap;
  }
  .contact-list {
    position: absolute;
    right: 34px;
    top: 308px;
    list-style: none;
    font-weight: 600;
    font-size: 20px;
    letter-spacing: 1.3px;
    white-space: nowrap;
  }
  .contact-item {
    display: flex;
    align-items: center;
    justify-content: flex-end;
    height: 42px;
  }
  .contact-item .icon-slot {
    width: 46px;
    display: flex;
    justify-content: flex-end;
  }
</style>
</head>
<body>
  <main class="canvas">
    <section class="business-card">
      <div class="brand-side">
        <span class="brand-name">Example Constructions</span>
      </div>
      <div class="accent-bar"></div>
      <div class="contact-side">
        <h1 class="person-name">YOUR NAME</h1>
        <ul class="contact-list">
          <li class="contact-item"><span>ABN 12 345 678 910</span><span class="icon-slot"></span></li>
          <li class="contact-item">
            <span>0400 000 000</span>
            <span class="icon-slot">
              <svg width="22" height="34" viewBox="0 0 22 34" aria-hidden="true">
                <rect x="1.5" y="1.5" width="19" height="31" rx="3" fill="none" stroke="#fff" stroke-width="2"/>
                <line x1="1.5" y1="6" x2="20.5" y2="6" stroke="#fff" stroke-width="1.5"/>
                <line x1="1.5" y1="27" x2="20.5" y2="27" stroke="#fff" stroke-width="1.5"/>
              </svg>
            </span>
          </li>
          <li class="contact-item">
            <span>EMAIL@EMAIL.COM.AU</span>
            <span class="icon-slot">
              <svg width="34" height="22" viewBox="0 0 34 22" aria-hidden="true">
                <rect x="0" y="0" width="34" height="22" fill="#fff"/>
                <polyline points="1,1 17,13 33,1" fill="none" stroke="#3d3d3d" stroke-width="2"/>
              </svg>
            </span>
          </li>
        </ul>
      </div>
    </section>
  </main>
</body>
</html>
```